Pella's Salon (Business Cards) Needed

I need a new business card for my hair salon based in Fairfax, VA called "Pella's Salon". I have been in business at the same location for the past 15 years, and have recently remodeled the place to be a little bit more upscale and modern. Previously, my clientele's were mostly men, but now I would like to attract more female clientele into my business. I would like the design to attract the female's attention with it's modern touch, flowery, freshness with just enough information and not too compact. Simple, clean and professional is the look.
Requirements
Must Have:
- The design should include:
Business name: Pella's Salon
Hairstylist/Owner Name: Pella Marsden
Phone Number: (555) 418-6307
Website: www.pellahairstudio.example
Address: 48153 Corwin Dale Lane
Fairfax, VA 20917
FRONT CARD should include:
- Logo (Business name)
- Slogan (Your beauty, our passion)
BACK CARD should include:
- Logo (Business name)
- Hairstyle name
- Phone number
- Website
- Address
Updates
Project Deadline Extended
Reason: There were some good submission for this project, but most of the submission were poorly designed, and did not have what I want. There isn't enough designs for me to choose from and not one of it stood out to me. I would like to extend it a bit longer to see if any other designer would step up to the plate, and deliver. Thank you.
Industry/Entity Type
Hair
Requirements
Must have
- The front side of the business card should only have the business name (Pella's Salon) and slogan, (Your beauty our passion) with a creative design.
The back side of the business card should have all the business information, and creative design that matches with the front, but not identical.
The first letter (V) in (Pella's) should have a flower design connected to it, which blends into the background design.
Nice to have
- Light color scheme.
Should not have
- The front, and back should not have the same design.
Do not include illustrations of a pair of scissors, combs or any objects in the design.
The design should not take the main focus from the business name and business information. It should blend well together... if that's possible.

```html
<!DOCTYPE html>
<html lang="en">
<head>
<meta charset="utf-8">
<title>Pella's Salon – Business Cards</title>
<link href="https://fonts.googleapis.com/css2?family=Roboto:wght@300;400;700&display=swap" rel="stylesheet">
<style>
  :root {
    --page: #2d2d2d;
    --card-dark: #232323;
    --card-orange: #e5711a;
    --pink: #f58a8a;
    --white: #ffffff;
    --ink: #2a2118;
    --ornament-dark: #3b3b3b;
    --ornament-orange: #f39c50;
  }
  html, body {
    margin: 0;
    padding: 0;
    width: 1025px;
    height: 1200px;
    overflow: hidden;
    background: var(--page);
    font-family: "Roboto", Arial, sans-serif;
  }
  .sheet {
    position: relative;
    width: 1025px;
    height: 1200px;
  }
  .card {
    position: absolute;
    left: 145px;
    width: 740px;
    height: 396px;
    overflow: hidden;
  }
  .card--dark { top: 133px; background: var(--card-dark); color: var(--white); }
  .card--orange { top: 648px; background: var(--card-orange); color: var(--white); }

  .card__header {
    position: absolute;
    right: 24px;
    top: 26px;
    text-align: right;
    font-size: 14px;
    line-height: 25px;
  }
  .card__name { font-weight: 700; font-size: 15px; }
  .card__phone { font-weight: 700; font-size: 13.5px; }
  .sep { margin: 0 9px; }
  .card--dark .sep--accent { color: var(--pink); }

  .logo {
    position: absolute;
    left: 120px;
    top: 96px;
    margin: 0;
    font-weight: 300;
    font-size: 88px;
    line-height: 1;
    letter-spacing: 1px;
    white-space: nowrap;
  }
  .card--dark .logo { color: var(--pink); }
  .card--orange .logo { color: var(--white); }

  .tagline {
    position: absolute;
    left: 254px;
    top: 220px;
    margin: 0;
    font-weight: 300;
    font-size: 27px;
    line-height: 1;
  }
  .card--dark .tagline { color: var(--white); }
  .card--dark .tagline em { font-style: normal; color: var(--pink); }
  .card--orange .tagline { color: var(--ink); }
  .card--orange .tagline em { font-style: normal; color: var(--white); }

  .card__address {
    position: absolute;
    left: 254px;
    top: 278px;
    font-size: 13px;
    line-height: 20px;
    font-style: normal;
  }
  .card__web { font-weight: 700; font-size: 13.5px; }
  .card--orange .card__address { color: var(--ink); }

  .ornament-band {
    position: absolute;
    left: 0;
    bottom: 0;
    width: 100%;
    height: 76px;
  }
  .card--dark .ornament-band {
    background: linear-gradient(to bottom, rgba(59,59,59,0), var(--ornament-dark) 70%);
  }
  .card--orange .ornament-band {
    background: linear-gradient(to bottom, rgba(243,156,80,0), var(--ornament-orange) 75%);
  }
</style>
</head>
<body>
<main class="sheet">

  <section class="card card--dark">
    <div class="card__header">
      <div><span class="card__name">PELLA MARSDEN -</span> Hairstylist <span class="sep">|</span><span class="card__phone">Phone: (555) 418-6307</span></div>
      <div>Mon-fri 10am-8pm <span class="sep sep--accent">|</span> Saturday 9am-7pm <span class="sep sep--accent">|</span> Sunday 11am-6pm</div>
    </div>
    <h1 class="logo">Pella's Salon</h1>
    <p class="tagline">Your <em>beauty</em>, our <em>passion</em></p>
    <address class="card__address">
      48153 Corwin Dale Lane, Fairfax, VA 20917<br>
      <span class="card__web">www.pellahairstudio.example</span>
    </address>
    <div class="ornament-band" role="img" aria-label="Faint floral flourish pattern along the bottom edge"></div>
  </section>

  <section class="card card--orange">
    <div class="card__header">
      <div><span class="card__name">PELLA MARSDEN -</span> Hairstylist <span class="sep">|</span><span class="card__phone">Phone: (555) 418-6307</span></div>
      <div>Mon-fri 10am-8pm <span class="sep">|</span> Saturday 9am-7pm <span class="sep">|</span> Sunday 11am-6pm</div>
    </div>
    <h2 class="logo">Pella's Salon</h2>
    <p class="tagline">Your beauty, our passion</p>
    <address class="card__address">
      48153 Corwin Dale Lane, Fairfax, VA 20917<br>
      <span class="card__web">www.pellahairstudio.example</span>
    </address>
    <div class="ornament-band" role="img" aria-label="Light orange floral flourish pattern along the bottom edge"></div>
  </section>

</main>
</body>
</html>
```